Brevard Trade Partners - we are Asian sourcing agents

We are sourcing agents based in the USA and we act as sourcing agents for clients in throughout the world. We focus primarily on custom sewn goods. So basically companies who do not have the in-house expertise to do it themselves, come to us and have us find suitable factories in Asia to do the production. We are middlemen. We find the factories...quote the project...manage the quality control and then deliver the goods directly to our customer's door. We pride ourselves in making the communication very easy and precise.

Current page is www.brevardtradepartners.com

I am not happy w/ the overall look. The spacing...the photos, the fonts...the design elements...the pictures. I want a cool, crisp design that conveys professionalism and clearly depicts/explains what we do.

Requirements
Must have
• use my logo....I like it...it was designed by someone on this website.
Nice to have
• a video/animation of the entire process would be wonderful. Showing initial contact with our office in the USA...then to my correspondence with my offices in Taiwan and in Hong Kong...and then back and fort w/ the customer.....and then between my people in Hong Kong/Taiwan with the local factories......and then a quote is generated and sent to my client......to samples being made and sent for approval.....to a PO being generated......to final samples being sent.....to the order being shipped and delivered to the clients warehouse. I was thinking of an animation showing arrows and text showing the back and forth communication and explaining how the process flows.

```html
<!DOCTYPE html>
<html lang="en">
<head>
<meta charset="utf-8">
<title>Brevard Trade Partners – Asian Outsourcing Made Easy</title>
<link href="https://fonts.googleapis.com/css2?family=Archivo+Black&family=Questrial&display=swap" rel="stylesheet">
<style>
  :root{
    --green:#7a9a12;
    --green-dark:#5f7a0a;
    --ink:#333333;
    --muted:#8a8a8a;
    --light:#f3f3f3;
    --band:#ebebeb;
    --white:#ffffff;
    --footer:#2e2e2e;
    --footer-base:#232323;
    --footer-text:#bdbdbd;
  }
  *{margin:0;padding:0;box-sizing:border-box}
  html,body{width:1200px;height:2576px;overflow:hidden;background:var(--white)}
  body{position:relative;font-family:"Questrial",Arial,sans-serif;color:var(--ink)}
  .abs{position:absolute}
  h1,h2,h3,.heading{font-family:"Archivo Black",Arial,sans-serif;font-weight:400}

  /* Hero */
  .hero{left:0;top:0;width:1200px;height:715px;overflow:hidden}
  .hero-photo{position:absolute;inset:0;background:linear-gradient(180deg,#2b2b2b 0%,#4a4a48 45%,#3a3a38 100%)}
  .hero-shade{position:absolute;inset:0}
  .brand{left:161px;top:40px;color:var(--white);font-size:34px;line-height:36px;letter-spacing:1px}
  .brand small{display:block;font-size:34px}
  .menu{left:966px;top:36px;display:flex;align-items:center;gap:14px;color:var(--white);font-size:14px;letter-spacing:1px}
  .menu-box{width:40px;height:34px;background:#111;display:flex;flex-direction:column;justify-content:center;gap:5px;padding:0 9px}
  .menu-box span{height:3px;background:var(--green)}
  .hero-title{left:155px;top:298px;color:var(--white);font-size:56px;line-height:72px;letter-spacing:1px}
  .hero-sub{left:163px;top:474px;color:var(--green);font-size:17px;letter-spacing:.5px}
  .btn{display:flex;align-items:center;justify-content:center;color:var(--white);font-size:17px;letter-spacing:.5px;background:var(--green);clip-path:polygon(9% 0,100% 0,100% 100%,0 100%)}
  .hero-btn{left:745px;top:547px;width:232px;height:41px}
  .dots{left:86px;top:700px;display:flex;gap:5px}
  .dots i{width:8px;height:8px;border-radius:50%;background:var(--white)}
  .dots i:first-child{background:var(--green)}

  /* What we do */
  .what-title{left:0;width:1200px;top:742px;text-align:center;color:var(--green);font-size:30px}
  .what-body{left:180px;width:840px;top:788px;text-align:center;color:#555;font-size:17px;line-height:21px}

  /* Sourcing */
  .sourcing{left:0;top:897px;width:1200px;height:449px;background:var(--light)}
  .src-title{left:153px;top:962px;color:var(--green);font-size:34px;line-height:38px}
  .src-rule{left:153px;top:1066px;width:132px;height:2px;background:#cfcfcf}
  .src-body{left:153px;top:1104px;width:360px;color:var(--muted);font-size:15px;line-height:21px}
  .read-more{left:153px;top:1265px;color:#777;font-size:12px;letter-spacing:.5px}
  .video{left:582px;top:964px;width:514px;height:266px;background:linear-gradient(180deg,#1d1d1d 0%,#4b4f55 45%,#6b6e70 100%);overflow:hidden}

  /* Products */
  .products-strip{left:0;top:1390px;width:360px;height:317px;background:linear-gradient(90deg,#dcdcda 0%,#f0f0ef 100%)}
  .products-band{left:0;top:1449px;width:1200px;height:258px;background:var(--light)}
  .view-btn{left:292px;top:1400px;width:217px;height:36px}
  .product{top:1478px;width:220px;text-align:center}
  .product-art{margin:0 auto;height:160px}
  .product-label{margin-top:20px;color:#8c8c8c;font-size:18px;letter-spacing:.5px}

  /* Testimonial */
  .quote-box{left:75px;top:1750px;width:990px;height:150px;background:#efefef;clip-path:polygon(14% 0,100% 0,86% 100%,0 100%)}
  .avatar{left:239px;top:1784px;width:68px;height:68px;border-radius:50%;background:radial-gradient(circle at 50% 45%,#9a8a80,#3c3a3a)}
  .quote-text{left:344px;top:1786px;width:480px;color:#555;font-size:17px;line-height:24px}
  .quote-mark{font-family:Georgia,serif;font-size:28px;color:#888;vertical-align:-6px}
  .quote-btn{left:859px;top:1851px;width:214px;height:39px}

  /* Location */
  .location{left:0;top:1950px;width:1200px;height:304px;background:var(--light)}
  .map{left:560px;top:1950px;width:640px;height:304px;background:linear-gradient(135deg,#e9e6dc 0%,#dfe3d5 50%,#ece8dd 100%);clip-path:polygon(30% 0,100% 0,100% 100%,0 100%)}
  .loc-title{left:207px;top:2007px;color:var(--green);font-size:32px}
  .contact{left:210px;color:var(--muted);font-size:13px;display:flex;align-items:center;gap:8px}
  .address{left:1003px;top:2110px;color:#333;font-size:13px;line-height:17px}

  /* Footer */
  .footer{left:0;top:2254px;width:1200px;height:262px;background:var(--footer)}
  .footer-base{left:0;top:2516px;width:1200px;height:60px;background:var(--footer-base);color:#9a9a9a;font-size:11px;text-align:center;line-height:60px}
  .f-col{top:2288px;color:var(--footer-text);font-size:11px;line-height:14.5px}
  .f-col h3{font-family:"Questrial",Arial,sans-serif;color:var(--white);font-size:15px;letter-spacing:.5px;margin-bottom:10px}
  .f-col ul{list-style:none}
</style>
</head>
<body>

<header class="abs hero">
  <div class="hero-photo" role="img" aria-label="Busy terminal hall with commuters, darkened photograph"></div>
  <svg class="hero-shade" width="1200" height="715" viewBox="0 0 1200 715">
    <polygon points="1165,0 1200,0 1200,30 705,715 680,715" fill="#1c1c1c"/>
    <polygon points="1200,30 1200,715 705,715" fill="#ffffff" fill-opacity="0.72"/>
  </svg>
  <div class="abs brand heading">BREVARD<small>TRADE PARTNERS</small></div>
  <nav class="abs menu"><div class="menu-box"><span></span><span></span><span></span></div>MENU</nav>
  <h1 class="abs hero-title">ASIAN OUTSOURCING<br>MADE EASY!</h1>
  <p class="abs hero-sub">CUSTOM SEWN GOODS MADE TO YOUR SPECIFICATIONS</p>
  <a class="abs btn hero-btn">REQUEST A QUOTE</a>
  <div class="abs dots"><i></i><i></i><i></i></div>
</header>

<section>
  <h2 class="abs what-title">WHAT WE DO</h2>
  <p class="abs what-body">We aren't tied to a particular sewing factory in China, India, Korea, Vietnam, &amp; Thailand. We instead have a long-established network of factories with whom we have gained trust and understanding. This arrangement allows us access to many specialized areas of expertise &amp; virtually unlimited capacity. Simply put, through our experience as a sewing contractor we know which factories to use for each specific job.</p>
</section>

<section class="abs sourcing"></section>
<h2 class="abs src-title">SOURCING CUSTOM<br>GOODS IN CHINA</h2>
<div class="abs src-rule"></div>
<p class="abs src-body">We outsource sewing services direct from China. Our long-established and extensive network of offshore factory-partners provides our clients with access to a wide variety of contract sewing expertise from Chinese manufacturers.</p>
<div class="abs read-more">READ MORE
  <svg width="22" height="12" viewBox="0 0 22 12" style="display:block;margin:6px 0 0 10px"><polyline points="2,2 11,9 20,2" fill="none" stroke="#888" stroke-width="1.5"/></svg>
</div>
<div class="abs video" role="img" aria-label="Video still of a large sewing factory floor with rows of workers">
  <svg width="514" height="266" viewBox="0 0 514 266">
    <circle cx="257" cy="125" r="24" fill="#fff" fill-opacity="0.55"/>
    <polygon points="250,113 250,137 268,125" fill="#fff"/>
    <rect x="12" y="240" width="490" height="3" fill="#fff" fill-opacity="0.35"/>
    <polygon points="14,247 14,257 22,252" fill="#fff"/>
    <text x="470" y="256" fill="#fff" font-size="11" font-family="Questrial, sans-serif">3:00</text>
  </svg>
</div>

<section>
  <div class="abs products-strip" role="img" aria-label="Faded photograph of a terminal hall"></div>
  <div class="abs products-band"></div>
  <svg class="abs" style="left:0;top:1390px" width="360" height="60" viewBox="0 0 360 60"><polygon points="0,0 360,0 360,59 300,59" fill="#ffffff"/></svg>
  <a class="abs btn view-btn">VIEW PRODUCTS</a>
  <div class="abs product" style="left:240px">
    <div class="product-art" role="img" aria-label="Black backpack" style="width:120px;background:linear-gradient(180deg,#3a3a3a,#111);border-radius:40px 40px 18px 18px"></div>
    <div class="product-label">BAGS</div>
  </div>
  <div class="abs product" style="left:570px">
    <div class="product-art" role="img" aria-label="Grey bicycle cover" style="width:170px;height:120px;margin-top:20px;background:linear-gradient(180deg,#d8d8d8,#9a9a9a);border-radius:60px 80px 12px 12px"></div>
    <div class="product-label">COVERS</div>
  </div>
  <div class="abs product" style="left:899px">
    <div class="product-art" role="img" aria-label="Blue and pink phone cases" style="width:150px;height:130px;margin-top:20px;background:linear-gradient(90deg,#2b55c8 0%,#2b55c8 48%,#c2268e 52%,#c2268e 100%);border-radius:10px"></div>
    <div class="product-label">CASES</div>
  </div>
</section>

<section>
  <div class="abs quote-box"></div>
  <div class="abs avatar" role="img" aria-label="Portrait of the company founder"></div>
  <p class="abs quote-text"><span class="quote-mark">“</span> Outsource Your Sewing Needs to Trusted Contractors in China Please contact us for immediate consultation regarding your outsourcing project <span class="quote-mark">”</span></p>
  <a class="abs btn quote-btn">REQUEST A QUOTE</a>
</section>

<section>
  <div class="abs location"></div>
  <div class="abs map" role="img" aria-label="Street map showing the office location"></div>
  <svg class="abs" style="left:970px;top:2060px" width="26" height="36" viewBox="0 0 26 36"><path d="M13 1C6 1 1 6 1 13c0 9 12 22 12 22s12-13 12-22C25 6 20 1 13 1z" fill="var(--green)"/><circle cx="13" cy="13" r="5" fill="#fff"/></svg>
  <div class="abs address">12 Harbor Lane Unit B-4<br>Dover, NH 03820</div>
  <h2 class="abs loc-title">LOCATION</h2>
  <div class="abs contact" style="top:2090px">
    <svg width="12" height="12" viewBox="0 0 24 24"><path d="M6.6 10.8a15 15 0 006.6 6.6l2.2-2.2c.3-.3.7-.4 1-.2 1.1.4 2.3.6 3.6.6.6 0 1 .4 1 1V20c0 .6-.4 1-1 1C10.6 21 3 13.4 3 4c0-.6.4-1 1-1h3.5c.6 0 1 .4 1 1 0 1.3.2 2.5.6 3.6.1.3 0 .7-.2 1z" fill="var(--green)"/></svg>
    555-010-4815
  </div>
  <div class="abs contact" style="top:2116px">
    <svg width="12" height="12" viewBox="0 0 24 24"><polygon points="2,11 22,3 15,22 12,14" fill="var(--green)"/></svg>
    Email: info@brevardtradepartners.com
  </div>
</section>

<footer>
  <div class="abs footer"></div>
  <div class="abs f-col" style="left:198px">
    <h3>CUSTOM BAGS</h3>
    <ul><li>Athletic Bags</li><li>Backpacks</li><li>Computer Bags</li><li>Cooler Bags</li><li>Cosmetic Bags</li><li>Handbags</li><li>Messenger Bags</li><li>Shopping Bags</li><li>Tool Bags</li><li>Travel Bags</li><li>Yoga Bags</li></ul>
  </div>
  <div class="abs f-col" style="left:401px">
    <h3>CUSTOM COVERS</h3>
    <ul><li>ATV Covers</li><li>Chair Covers</li><li>Equipment Covers</li><li>Golf Cart Covers</li><li>Motorcycle Covers</li><li>Outdoor Furniture</li><li>Covers</li><li>Outdoor Grill Cover</li><li>Personal Watercraft</li><li>Covers</li><li>Snowmobile Covers</li></ul>
  </div>
  <div class="abs f-col" style="left:620px">
    <h3>CUSTOM GLOVES</h3>
    <ul><li>Batting Gloves</li><li>Garden Gloves</li><li>Mechanic Gloves</li><li>Safety Gloves</li><li>Ski Gloves</li></ul>
    <h3 style="margin-top:18px">CUSTOM CASES</h3>
    <ul><li>Cosmetic Cases</li><li>Phone Cases</li><li>Tool Bags and Tool</li><li>Cases</li></ul>
  </div>
  <div class="abs f-col" style="left:829px">
    <h3>CUSTOM SEWN GOODS</h3>
    <ul><li>Pet Collars, Leashes, &amp;</li><li>Harnesses</li><li>Socks</li></ul>
    <h3 style="margin-top:50px">CUSTOM SPORTING GOODS</h3>
    <ul><li>Yoga Mats</li><li>Yoga Gear and</li><li>Accessories</li></ul>
  </div>
  <div class="abs footer-base">© 2015 Brevard Trade Partners, LLC. | USA – Hong Kong – Taipei</div>
</footer>

</body>
</html>
```